The most modern business card ever !!!

Our company call “Vendalo”. Vendalo is a technology company specialized in cruises solutions. Out main product is a platform to reserve cruises. This is a revolutionary platform that make easier to travel agencies and final users to reserve cruises across dozen companies like tibba, wernu, hpv, dgb, etc..We are a “start up”, with a young team of developers and we want to transmit it.. For it, we want something different, a modern business card that represent cruises and technology.. When someone receive this card, this person should say: wowww this is different… this is modern… this is a cruise related company..
- diferent, modern
- traditions business card

```html
<!DOCTYPE html>
<html lang="en">
<head>
<meta charset="utf-8">
<title>Vendalo – Business Card</title>
<link href="https://fonts.googleapis.com/css2?family=Open+Sans:wght@400;600;700&display=swap" rel="stylesheet">
<style>
  :root {
    --backdrop: #4a423d;
    --card: #0e0e0f;
    --card-edge: #1b1b1c;
    --white: #f4f4f4;
    --muted: #b9b9b9;
    --accent: #2ea3dd;
    --divider: #2a2a2b;
  }
  * { margin: 0; padding: 0; box-sizing: border-box; }
  html, body {
    width: 1200px; height: 844px; overflow: hidden;
    background: var(--backdrop);
    font-family: "Open Sans", Arial, sans-serif;
  }
  .sheet {
    position: relative; width: 1200px; height: 844px;
    display: flex; align-items: center; justify-content: center; gap: 60px;
  }
  .card {
    position: relative; width: 520px; height: 300px;
    background: var(--card);
    border: 1px solid var(--card-edge);
    box-shadow: 0 14px 30px rgba(0,0,0,.45);
  }
  .wordmark {
    color: var(--white); font-weight: 600; letter-spacing: 1px; line-height: 1;
  }
  .card-front .wordmark {
    position: absolute; left: 36px; top: 132px; font-size: 44px;
  }
  .card-front .divider {
    position: absolute; left: 282px; top: 40px; bottom: 40px;
    width: 1px; background: var(--divider);
  }
  .contact {
    position: absolute; left: 300px; top: 48px; right: 16px;
    color: var(--muted); font-size: 13px; line-height: 1.35;
  }
  .contact .name {
    color: var(--accent); font-weight: 700; font-size: 15px; letter-spacing: .5px;
  }
  .contact .role { margin-bottom: 8px; }
  .contact ul { list-style: none; }
  .contact li { display: flex; align-items: center; gap: 7px; }
  .contact svg { width: 11px; height: 11px; fill: var(--accent); flex: none; }
  .contact .address { margin-top: 8px; }
  .card-back { display: flex; align-items: center; justify-content: center; }
  .card-back .wordmark { font-size: 52px; color: #d8d8d8; }
</style>
</head>
<body>
<main class="sheet">
  <section class="card card-front">
    <div class="wordmark">Vendalo</div>
    <div class="divider"></div>
    <div class="contact">
      <div class="name">MARCUS HALE</div>
      <div class="role">Managing Director</div>
      <ul>
        <li><svg viewBox="0 0 12 12"><path d="M1 4c0-2 2-3 5-3s5 1 5 3l-2 1-1-2H4L3 5zM2 6h8v5H2z"/></svg>044-555 210 347</li>
        <li><svg viewBox="0 0 12 12"><path d="M3 0h6v12H3zM4 1v9h4V1z"/></svg>044-555 210 347</li>
        <li><svg viewBox="0 0 12 12"><path d="M0 2h12v8H0zM1 3l5 4 5-4v-.2H1z"/></svg>hello@vendalo.com</li>
        <li><svg viewBox="0 0 12 12"><circle cx="6" cy="6" r="5.5"/></svg>www.vendalo.com</li>
      </ul>
      <div class="address">12345, Address Goes Here<br>Country Name, 123456.</div>
    </div>
  </section>
  <section class="card card-back">
    <div class="wordmark">Vendalo</div>
  </section>
</main>
</body>
</html>
```